Vantiqo custom business card design

Need a authentic, innovative business card design for a new mobile app business. I am uploading a few screen images from our app for you to view. I would like app design theme to match business card design. I can also send logo images.

```html
<!DOCTYPE html>
<html lang="en">
<head>
<meta charset="utf-8">
<title>Vantiqo business card</title>
<link rel="stylesheet" href="https://fonts.googleapis.com/css2?family=Work+Sans:wght@400;500;800&display=swap">
<style>
  :root {
    --stage: #9b9b9b;
    --card-dark: #242424;
    --card-light: #ffffff;
    --purple: #5d2a91;
    --ink: #1f1f1f;
    --muted: #333333;
  }
  * { margin: 0; padding: 0; box-sizing: border-box; }
  html, body {
    width: 1200px; height: 930px; overflow: hidden;
    background: var(--stage);
    font-family: "Work Sans", sans-serif;
  }
  .canvas { position: relative; width: 1200px; height: 930px; }

  .card {
    position: absolute;
    width: 700px; height: 400px;
    border-radius: 26px;
    overflow: hidden;
  }

  /* Back side */
  .card-back {
    left: 110px; top: 50px;
    background: var(--card-dark);
    display: flex; align-items: center; justify-content: center; gap: 18px;
  }
  .card-back .brand-dot { width: 44px; height: 44px; border-radius: 50%; background: var(--purple); }
  .card-back .brand-name {
    color: #ffffff; font-weight: 800; font-size: 64px; letter-spacing: 0.5px;
  }

  /* Front side */
  .card-front {
    left: 390px; top: 480px;
    background: var(--card-light);
  }
  .front-brand {
    position: absolute; right: 46px; top: 54px;
    display: flex; align-items: center; gap: 12px;
  }
  .front-brand .brand-dot { width: 30px; height: 30px; border-radius: 50%; background: var(--purple); }
  .front-brand .brand-name { color: var(--ink); font-weight: 800; font-size: 44px; }

  .rule-long {
    position: absolute; left: 300px; right: 46px; top: 150px;
    height: 2px; background: var(--purple);
  }
  .accent-bar {
    position: absolute; left: 0; top: 186px;
    width: 14px; height: 46px; background: var(--purple);
  }
  .person { position: absolute; left: 46px; top: 168px; }
  .person-name {
    color: var(--purple); font-weight: 500; font-size: 30px;
    text-transform: uppercase; letter-spacing: 0.2px; line-height: 1.1;
  }
  .person-role { color: var(--muted); font-size: 19px; margin-top: 2px; }
  .rule-short {
    position: absolute; left: 46px; width: 250px; top: 254px;
    height: 2px; background: var(--purple);
  }

  .contacts {
    position: absolute; left: 46px; top: 272px;
    list-style: none;
  }
  .contacts li {
    display: flex; align-items: center; gap: 16px;
    color: var(--ink); font-size: 20px; line-height: 28px;
  }
  .contacts svg { width: 14px; height: 14px; flex: none; }

  .address {
    position: absolute; right: 46px; top: 176px;
    text-align: right; font-style: normal;
    color: var(--ink); font-size: 20px; line-height: 28px;
  }
</style>
</head>
<body>
<main class="canvas">

  <section class="card card-back" aria-label="Card back">
    <span class="brand-dot"></span>
    <span class="brand-name">Vantiqo</span>
  </section>

  <section class="card card-front" aria-label="Card front">
    <div class="front-brand">
      <span class="brand-dot"></span>
      <span class="brand-name">Vantiqo</span>
    </div>

    <div class="rule-long"></div>
    <div class="accent-bar"></div>

    <div class="person">
      <p class="person-name">Daniel Harper</p>
      <p class="person-role">Director</p>
    </div>
    <div class="rule-short"></div>

    <ul class="contacts">
      <li>
        <svg viewBox="0 0 14 14" fill="none" stroke="#5d2a91" stroke-width="1.6"><rect x="3.5" y="1" width="7" height="12" rx="1.2"/><line x1="6" y1="11" x2="8" y2="11"/></svg>
        (555) 014-2286
      </li>
      <li>
        <svg viewBox="0 0 14 14" fill="#5d2a91"><path d="M3 1.2l2.2 0 1 3-1.5 1.2c.8 1.6 2 2.8 3.6 3.6L9.5 7.5l3 1v2.3c0 .7-.6 1.2-1.3 1.2C5.6 11.7 2 8.2 1.8 2.5 1.8 1.8 2.3 1.2 3 1.2z"/></svg>
        (555) 014-7392
      </li>
      <li>
        <svg viewBox="0 0 14 14" fill="none" stroke="#5d2a91" stroke-width="1.4"><rect x="1" y="3" width="12" height="8.5" rx="1"/><path d="M1.5 3.5L7 8l5.5-4.5"/></svg>
        info@vantiqo.com
      </li>
      <li>
        <svg viewBox="0 0 14 14" fill="none" stroke="#5d2a91" stroke-width="1.2"><circle cx="7" cy="7" r="5.8"/><ellipse cx="7" cy="7" rx="2.6" ry="5.8"/><line x1="1.2" y1="7" x2="12.8" y2="7"/><line x1="2" y1="4" x2="12" y2="4"/><line x1="2" y1="10" x2="12" y2="10"/></svg>
        www.vantiqo.com
      </li>
    </ul>

    <address class="address">
      1820 Harbor Lane<br>
      Lakeview, FL 30000
    </address>
  </section>

</main>
</body>
</html>
```